Corvel Capital LLC

Need Professional Business cards for New Investment Fund

Target Market(s)

High Quality investors

Industry/Entity Type

Financial

Contact Information for Business Card

Phone Number +1 555 284 6190
Name Lukas Varenko
Title Fund Manager
email lv@FundCorvel.com
Website www.FundCorvel.com

Colors

Designer to choose colors to be used in the design.

Requirements
Must have
• Must have our Logo and all of the above. Must be made so lettering and loge can be raised

```html
<!DOCTYPE html>
<html lang="en">
<head>
<meta charset="utf-8">
<title>Fund Manager – Business Card</title>
<link rel="stylesheet" href="https://fonts.googleapis.com/css2?family=Questrial&display=swap">
<style>
  :root {
    --backdrop: #d9d9d9;
    --card-dark: #4c584b;
    --card-dark-deep: #3f4a3f;
    --card-light: #ffffff;
    --accent: #1fd400;
    --ink-light: #eef0ee;
    --ink-dark: #3f4a3f;
    --divider: #b8bfb8;
  }
  * { box-sizing: border-box; margin: 0; padding: 0; }
  html, body {
    width: 1200px;
    height: 801px;
    overflow: hidden;
  }
  body {
    background: var(--backdrop);
    font-family: "Questrial", "Century Gothic", sans-serif;
    display: flex;
    align-items: center;
    justify-content: center;
    gap: 60px;
  }
  .card {
    width: 520px;
    height: 297px;
    border: 2px solid var(--accent);
    box-shadow: 0 18px 30px rgba(0,0,0,0.18);
    position: relative;
    overflow: hidden;
  }
  .card--front {
    background: linear-gradient(160deg, var(--card-dark-deep), var(--card-dark));
    display: flex;
    align-items: center;
    justify-content: center;
    gap: 22px;
  }
  .identity { text-align: right; }
  .identity__name {
    color: var(--accent);
    font-size: 25px;
    letter-spacing: 0.5px;
    line-height: 1.1;
    white-space: nowrap;
  }
  .identity__title {
    color: var(--ink-light);
    font-size: 16px;
    margin-top: 2px;
  }
  .divider {
    width: 1px;
    height: 74px;
    background: var(--divider);
  }
  .contacts {
    list-style: none;
    color: var(--ink-light);
    font-size: 13.5px;
    line-height: 1.55;
    white-space: nowrap;
  }
  .contacts li {
    display: flex;
    align-items: center;
    gap: 8px;
  }
  .contacts svg {
    width: 11px;
    height: 11px;
    fill: var(--accent);
    flex: none;
  }
  .card--back {
    background: var(--card-light);
    display: flex;
    align-items: center;
    justify-content: center;
  }
  .brand {
    display: flex;
    align-items: center;
    gap: 14px;
  }
  .brand__mark {
    width: 22px;
    height: 22px;
    background: var(--accent);
  }
  .brand__name {
    color: var(--ink-dark);
    font-size: 42px;
    letter-spacing: 4px;
    white-space: nowrap;
  }
</style>
</head>
<body>
  <section class="card card--front">
    <div class="identity">
      <p class="identity__name">Lukas Varenko</p>
      <p class="identity__title">Fund Manager</p>
    </div>
    <div class="divider"></div>
    <ul class="contacts">
      <li>
        <svg viewBox="0 0 12 12" aria-hidden="true"><path d="M2.4 0.8l2 2.2-1 1.4c0.7 1.6 1.8 2.7 3.3 3.4l1.4-1 2.2 2-1.2 2.2C5 10.6 1.4 7 0.8 2z"/></svg>
        +1 555 284 6190
      </li>
      <li>
        <svg viewBox="0 0 12 12" aria-hidden="true"><path d="M0 2h12v8H0z M0.8 2.6L6 6.6l5.2-4" stroke="#3f4a3f" stroke-width="0.9"/></svg>
        lv@FundCorvel.com
      </li>
      <li>
        <svg viewBox="0 0 12 12" aria-hidden="true"><circle cx="6" cy="6" r="6"/><path d="M3.5 6.5l2-3 1 2 1.6-1" stroke="#3f4a3f" stroke-width="1" fill="none"/></svg>
        www.FundCorvel.com
      </li>
    </ul>
  </section>

  <section class="card card--back">
    <div class="brand">
      <span class="brand__mark"></span>
      <span class="brand__name">KESTIVAR</span>
    </div>
  </section>
</body>
</html>
```